Business Card Design

Buy and sell properties
Buy and rehab properties
Buy properties for cash
That is what I do but do need a logo
looking for some type of logo or design on it
Just started business
Back of card should say something like BUY HOUSES CASH
Overview: it is a new company. Basically I buy properties wholesale and fix them up and sell them or sell them to other fix and flippers
Background: company is new so not any background
Market: is basically anyone selling a house or buying a house. Someone that needs to sell house fast. Basically I am a cash home buyer!!!

Updates
Email on card should be:   harborlanerealtyinc@mailnest.com

Industry/Entity Type
House
Contact Information for Business Card
Harbor Lane Realty Inc
PO Box 718296
Coral Mill Key FL 33071

Dwight Kallum
harborlanerealtyinc@mailnest.com
305-271-5589

```html
<!DOCTYPE html>
<html lang="en">
<head>
<meta charset="utf-8">
<title>Harbor Lane Realty Inc — Business Card</title>
<link rel="stylesheet" href="https://fonts.googleapis.com/css2?family=Roboto:wght@300;400&display=swap">
<style>
  :root {
    --ink: #0a0a0a;
    --paper: #ffffff;
    --accent: #2b7bbd;
    --backdrop: #d9d6d1;
    --muted: #e8e8e8;
  }
  * { box-sizing: border-box; margin: 0; padding: 0; }
  html, body { width: 1200px; height: 848px; overflow: hidden; }
  body {
    background: var(--backdrop);
    font-family: "Roboto", Helvetica, Arial, sans-serif;
    font-weight: 300;
    display: flex;
    align-items: center;
    justify-content: center;
    gap: 40px;
  }
  .card {
    position: relative;
    width: 540px;
    height: 310px;
    border-radius: 18px;
    overflow: hidden;
    background: var(--paper);
    box-shadow: 0 10px 28px rgba(0,0,0,.22);
  }
  .card-shape { position: absolute; inset: 0; width: 100%; height: 100%; }

  /* front */
  .brand {
    position: absolute;
    display: flex; align-items: center; gap: 12px;
  }
  .brand--front { left: 30px; top: 118px; width: 200px; }
  .brand-dot { width: 30px; height: 30px; border-radius: 50%; background: var(--accent); flex: none; }
  .brand-name {
    font-size: 24px; font-weight: 400; line-height: 1.1;
    color: var(--ink); text-transform: uppercase; letter-spacing: .3px;
  }
  .holder-name {
    position: absolute; left: 318px; top: 40px;
    color: var(--paper); font-size: 22px; font-weight: 300;
  }
  .contact-list {
    position: absolute; left: 316px; top: 196px;
    list-style: none; display: flex; flex-direction: column; gap: 9px;
  }
  .contact-item {
    display: flex; align-items: center; gap: 8px;
    color: var(--muted); font-size: 11px; white-space: nowrap;
  }
  .contact-icon {
    width: 20px; height: 20px; border-radius: 4px;
    background: var(--paper); flex: none;
    display: flex; align-items: center; justify-content: center;
  }
  .contact-icon svg { width: 14px; height: 14px; }

  /* back */
  .tagline {
    position: absolute; left: 36px; top: 140px;
    font-size: 24px; font-weight: 400; color: var(--ink);
    letter-spacing: .5px; white-space: nowrap;
  }
  .brand--reverse { left: 362px; top: 104px; width: 160px; gap: 10px; }
  .brand--reverse .brand-dot { width: 24px; height: 24px; background: var(--paper); }
  .brand--reverse .brand-name { color: var(--paper); font-size: 19px; }
</style>
</head>
<body>

<section class="card card--front" aria-label="Card front">
  <svg class="card-shape" viewBox="0 0 540 310" aria-hidden="true">
    <polygon points="232,0 240,0 308,310 300,310" fill="#0a0a0a"/>
    <polygon points="248,0 540,0 540,310 316,310" fill="#0a0a0a"/>
  </svg>
  <div class="brand brand--front">
    <span class="brand-dot"></span>
    <span class="brand-name">Harbor Lane Realty Inc</span>
  </div>
  <p class="holder-name">Dwight Kallum</p>
  <ul class="contact-list">
    <li class="contact-item">
      <span class="contact-icon"><svg viewBox="0 0 24 24"><path fill="#2b7bbd" d="M6.6 10.8a15.1 15.1 0 0 0 6.6 6.6l2.2-2.2c.3-.3.7-.4 1-.2 1.1.4 2.3.6 3.6.6.6 0 1 .4 1 1V20c0 .6-.4 1-1 1A17 17 0 0 1 3 4c0-.6.4-1 1-1h3.5c.6 0 1 .4 1 1 0 1.3.2 2.5.6 3.6.1.3 0 .7-.2 1z"/></svg></span>
      305-271-5589
    </li>
    <li class="contact-item">
      <span class="contact-icon"><svg viewBox="0 0 24 24"><rect x="3" y="6" width="18" height="12" rx="1" fill="#2b7bbd"/><path d="M3 7l9 6 9-6" fill="none" stroke="#fff" stroke-width="1.6"/></svg></span>
      harborlanerealtyinc@mailnest.com
    </li>
    <li class="contact-item">
      <span class="contact-icon"><svg viewBox="0 0 24 24"><path fill="#2b7bbd" d="M12 2a7 7 0 0 0-7 7c0 5 7 13 7 13s7-8 7-13a7 7 0 0 0-7-7zm0 9.5A2.5 2.5 0 1 1 12 6.5a2.5 2.5 0 0 1 0 5z"/></svg></span>
      718296 Coral Mill Key FL 33071
    </li>
  </ul>
</section>

<section class="card card--back" aria-label="Card back">
  <svg class="card-shape" viewBox="0 0 540 310" aria-hidden="true">
    <polygon points="280,310 288,310 358,0 350,0" fill="#0a0a0a"/>
    <polygon points="302,310 540,310 540,0 372,0" fill="#0a0a0a"/>
  </svg>
  <p class="tagline">BUY HOUSES CASH</p>
  <div class="brand brand--reverse">
    <span class="brand-dot"></span>
    <span class="brand-name">Harbor Lane Realty Inc</span>
  </div>
</section>

</body>
</html>
```